My project benefits Military, First Responders, Police, Fire, and Educators.

Contact Information for Business Card

2 Sided appointment card. Visual side will have my head shot with "Brisk Lantern" in a bold graffic/text. I am picturing maybe the headshot applied to a filter that has a matrix effect where the picture is made up of data/numbers flowing vertically through the photo. I am of course open to other concepts as well. Side two will have contact info presented in an attractive visual complimenting the front.

```html
<!DOCTYPE html>
<html lang="en">
<head>
<meta charset="UTF-8">
<title>Brisk Lantern – Appointment Card</title>
<link rel="stylesheet" href="https://fonts.googleapis.com/css2?family=Source+Sans+3:wght@400;600;700&display=swap">
<style>
  :root {
    --backdrop: #e6e7ea;
    --card-dark: #161718;
    --card-dark-edge: #26282b;
    --card-light: #fbfbfb;
    --brand-blue: #1f5fb8;
    --text-light: #f2f2f2;
    --rule: #4a4a4a;
    --photo-navy: #1c2a44;
    --photo-warm: #8a6a55;
  }
  * { margin: 0; padding: 0; box-sizing: border-box; }
  html, body { width: 1200px; height: 900px; overflow: hidden; }
  body {
    background: var(--backdrop);
    font-family: "Source Sans 3", Arial, sans-serif;
    position: relative;
  }
  .card {
    position: absolute;
    top: 301px;
    width: 520px;
    height: 297px;
    border-radius: 18px;
    overflow: hidden;
    box-shadow: 0 10px 30px rgba(0,0,0,0.18);
  }
  /* Front: portrait side */
  .card--front {
    left: 60px;
    background: linear-gradient(160deg, var(--card-dark-edge) 0%, var(--card-dark) 60%);
  }
  .portrait {
    position: absolute;
    left: 0;
    bottom: 0;
    width: 320px;
    height: 230px;
    background:
      radial-gradient(ellipse 38% 42% at 38% 38%, var(--photo-warm) 0%, rgba(138,106,85,0) 100%),
      radial-gradient(ellipse 70% 55% at 45% 100%, var(--photo-navy) 0%, rgba(28,42,68,0) 100%);
  }
  .contact {
    position: absolute;
    left: 300px;
    top: 58px;
    color: var(--text-light);
  }
  .contact__name {
    color: var(--brand-blue);
    font-size: 19px;
    font-weight: 600;
    line-height: 1.1;
  }
  .contact__role {
    font-size: 14px;
    margin-bottom: 14px;
  }
  .contact__list { list-style: none; }
  .contact__item {
    display: flex;
    align-items: center;
    gap: 10px;
    font-size: 14px;
    line-height: 1.35;
  }
  .contact__icon { width: 11px; height: 11px; flex: none; }

  /* Back: appointment side */
  .card--back {
    left: 620px;
    background: var(--card-light);
  }
  .brand {
    position: absolute;
    top: 40px;
    left: 0;
    width: 100%;
    text-align: center;
    color: var(--brand-blue);
    font-size: 40px;
    font-weight: 700;
    letter-spacing: -0.5px;
  }
  .appointment {
    position: absolute;
    left: 36px;
    right: 36px;
    top: 130px;
  }
  .appointment__row {
    display: flex;
    align-items: flex-end;
    gap: 12px;
    height: 34px;
  }
  .appointment__label {
    color: var(--brand-blue);
    font-size: 18px;
    font-weight: 700;
    line-height: 1;
  }
  .appointment__line {
    flex: 1;
    border-bottom: 2px dotted var(--rule);
    margin-bottom: 3px;
  }
  .appointment__note {
    margin-top: 20px;
    color: var(--brand-blue);
    font-size: 14px;
    font-weight: 700;
  }
</style>
</head>
<body>
  <section class="card card--front">
    <div class="portrait" role="img" aria-label="Head-and-shoulders portrait of the managing director in a dark suit and striped tie"></div>
    <div class="contact">
      <p class="contact__name">Daniel Reyes</p>
      <p class="contact__role">Managing Director</p>
      <ul class="contact__list">
        <li class="contact__item">
          <svg class="contact__icon" viewBox="0 0 12 12" aria-hidden="true"><path fill="#1f5fb8" d="M2.5 0.8l2 2-1.2 1.4c.7 1.5 2 2.8 3.5 3.5l1.4-1.2 2 2-1.3 1.9C5 10.2 1.8 7 1 2.1z"/></svg>
          <span>044-555 210 347</span>
        </li>
        <li class="contact__item">
          <svg class="contact__icon" viewBox="0 0 12 12" aria-hidden="true"><rect x="0.5" y="2" width="11" height="8" fill="#1f5fb8"/><path d="M0.5 2l5.5 4.5L11.5 2" fill="none" stroke="#161718" stroke-width="1"/></svg>
          <span>info@brisklantern.com</span>
        </li>
        <li class="contact__item">
          <svg class="contact__icon" viewBox="0 0 12 12" aria-hidden="true"><circle cx="6" cy="6" r="5.5" fill="#1f5fb8"/><path d="M0.5 6h11M6 0.5c-2.5 3-2.5 8 0 11M6 0.5c2.5 3 2.5 8 0 11" fill="none" stroke="#161718" stroke-width="0.8"/></svg>
          <span>www.brisklantern.com</span>
        </li>
      </ul>
    </div>
  </section>

  <section class="card card--back">
    <p class="brand">Brisk Lantern</p>
    <div class="appointment">
      <div class="appointment__row">
        <span class="appointment__label">Appointment</span>
        <span class="appointment__line"></span>
      </div>
      <div class="appointment__row"><span class="appointment__line"></span></div>
      <div class="appointment__row"><span class="appointment__line"></span></div>
      <p class="appointment__note">If unable to keep appointment, kindly give 24hrs notice.</p>
    </div>
  </section>
</body>
</html>
```